BrindleStaffing Business Card Design

We are a staffing company finding positions for dedicated nurses and physicians.

Target Market(s)

Business Professionals

Industry/Entity Type

Staffing

Contact Information for Business Card

Gordon Pratley
Chairman
417 39th Avenue South
SAINT PETERSBURG FL 33712
813-555-4172 Mobile
813-555-8036 Fax
gpratley@brindlestaffing.com
www.brindlestaffing.com

Font styles to use
Sans Serif

Colors
fbee3e
f04a50
f37122

Requirements
Must have
• Logo Attached, see colors below. We'd like to see Yellow, Orange and Red.

```html
<!DOCTYPE html>
<html lang="en">
<head>
<meta charset="utf-8">
<title>BrindleStaffing Business Card</title>
<link href="https://fonts.googleapis.com/css2?family=Open+Sans:wght@400;600;700&display=swap" rel="stylesheet">
<style>
  :root {
    --page-bg: #eceae6;
    --card-white: #ffffff;
    --brand-yellow: #fbee3e;
    --brand-red: #f04a50;
    --brand-orange: #f37122;
    --text-white: #ffffff;
    --shadow: rgba(0, 0, 0, 0.22);
  }
  * { margin: 0; padding: 0; box-sizing: border-box; }
  html, body {
    width: 1200px;
    height: 768px;
    overflow: hidden;
    background: var(--page-bg);
    font-family: "Open Sans", sans-serif;
  }
  .card-set {
    position: absolute;
    top: 229px;
    left: 40px;
    display: flex;
    gap: 40px;
  }
  .card {
    position: relative;
    width: 540px;
    height: 310px;
    border-radius: 18px;
    overflow: hidden;
    box-shadow: 0 10px 24px var(--shadow);
  }
  .card-front { background: var(--card-white); }
  .card-back {
    background: var(--brand-red);
    display: flex;
    align-items: center;
    justify-content: center;
  }
  .contact-arc {
    position: absolute;
    inset: 0;
  }
  .wordmark {
    font-family: "Open Sans", sans-serif;
    font-weight: 700;
    letter-spacing: -0.5px;
    display: flex;
    align-items: center;
    gap: 8px;
  }
  .wordmark-dot {
    width: 12px;
    height: 12px;
    border-radius: 50%;
  }
  .card-front .wordmark {
    position: absolute;
    top: 46px;
    right: 40px;
    font-size: 36px;
    color: var(--brand-red);
  }
  .card-front .wordmark-dot { background: var(--brand-orange); }
  .card-back .wordmark {
    font-size: 56px;
    color: var(--text-white);
  }
  .card-back .wordmark-dot {
    width: 16px;
    height: 16px;
    background: var(--brand-yellow);
  }
  .contact-block {
    position: absolute;
    left: 92px;
    top: 142px;
    color: var(--text-white);
  }
  .person-name {
    font-size: 21px;
    font-weight: 700;
    line-height: 1.15;
  }
  .person-title {
    font-size: 13px;
    font-weight: 600;
    line-height: 1.3;
    margin-bottom: 8px;
  }
  .address {
    font-size: 12.5px;
    line-height: 1.35;
    margin-bottom: 5px;
  }
  .contact-list { list-style: none; }
  .contact-list li {
    display: flex;
    align-items: center;
    gap: 8px;
    font-size: 12.5px;
    line-height: 1.4;
  }
  .contact-icon {
    width: 12px;
    height: 12px;
    flex: none;
  }
</style>
</head>
<body>
  <main class="card-set">
    <section class="card card-front" aria-label="Business card front">
      <svg class="contact-arc" viewBox="0 0 540 310" aria-hidden="true">
        <circle cx="220" cy="430" r="320" fill="var(--brand-orange)" stroke="var(--brand-yellow)" stroke-width="5"/>
      </svg>

      <div class="wordmark">BrindleStaffing<span class="wordmark-dot"></span></div>

      <div class="contact-block">
        <p class="person-name">Gordon Pratley</p>
        <p class="person-title">Chairman</p>
        <p class="address">417 39th Avenue South<br>SAINT PETERSBURG FL 33712</p>
        <ul class="contact-list">
          <li>
            <svg class="contact-icon" viewBox="0 0 12 12" aria-label="Mobile"><rect x="3" y="0.5" width="6" height="11" rx="1" fill="none" stroke="#fff" stroke-width="1.2"/><circle cx="6" cy="9.5" r="0.7" fill="#fff"/></svg>
            813-555-4172
          </li>
          <li>
            <svg class="contact-icon" viewBox="0 0 12 12" aria-label="Fax"><rect x="1" y="4" width="10" height="6" rx="1" fill="#fff"/><rect x="3" y="1" width="6" height="3" fill="none" stroke="#fff" stroke-width="1"/></svg>
            813-555-8036
          </li>
          <li>
            <svg class="contact-icon" viewBox="0 0 12 12" aria-label="Email"><rect x="0.5" y="2" width="11" height="8" fill="#fff"/><path d="M0.5 2 L6 6.5 L11.5 2" fill="none" stroke="var(--brand-orange)" stroke-width="1"/></svg>
            gpratley@brindlestaffing.com
          </li>
          <li>
            <svg class="contact-icon" viewBox="0 0 12 12" aria-label="Website"><circle cx="6" cy="6" r="5.5" fill="#fff"/><path d="M0.5 6 H11.5 M6 0.5 C3 3 3 9 6 11.5 M6 0.5 C9 3 9 9 6 11.5" fill="none" stroke="var(--brand-orange)" stroke-width="0.8"/></svg>
            www.brindlestaffing.com
          </li>
        </ul>
      </div>
    </section>

    <section class="card card-back" aria-label="Business card back">
      <div class="wordmark">BrindleStaffing<span class="wordmark-dot"></span></div>
    </section>
  </main>
</body>
</html>
```